Tovami Easy to modify Email Template

I need an email template created that can be easily modified for each new email sent. What I'm trying to accomplish is a look and feel that is consistent with each email I send out. In a perfect world, I'd like a template to use as a newsletter/informational with product/service pictures and an easy way to create the text to go with it. Then I'd also like a second email that is for letting my clients know there is a promotion or sale going on. Again, something that can he easily modified. I use mail chimp and MindBody as my platform for emailing. If possible, I'd like a pop-up box or dialog box that will ask the ready to opt-in with their name and email address.
I tried to have this done last year on ArtBazaar but we could never get it to work on Mail Chimp - the black box on the attachment would never display or capture email addresses.
What was created for me last year on ArtBazaar is great with matching colors and different sections. What would be great, if possible, is to create a template where I can add different photos in the same section, different verbiage in the same section, etc.
I hope I explained it well enough.
Updates

Target Market(s)

Target market is female - 30 to 65 years old

Industry/Entity Type

Health And Wellness

Font styles to use
Serif
Other font styles liked:
• lato

Requirements
Must have
• 1) must be able to be edited (and not by a designer/programmer)
2) must have an option to capture email addresses so people can opt-in to future email campaigns
3) must have a Zen feel to it. We are a medical spa - a very relaxed office space
4) not be too busy
Nice to have
• I hope this isn't asking too much, but the email needs to be able to run on MailChimp with no glitches. I would like the template(s) to be easily modified. Maybe keep the header and footer the same, back ground the same, and just sections that can be modified. Keep the colors to match my logo and the design from last year.

```html
<!DOCTYPE html>
<html lang="en">
<head>
<meta charset="utf-8">
<title>Tovami Medispa Newsletter</title>
<link rel="stylesheet" href="https://fonts.googleapis.com/css2?family=Montserrat:wght@300;400;500;600&display=swap">
<style>
:root{
  --leaf:#a9cf38;
  --mint:#85d1c6;
  --white:#ffffff;
  --forest-deep:#121b14;
  --forest:#2c3f2e;
  --field:#ffffff;
  --field-text:#6d6d6d;
}
*{margin:0;padding:0;box-sizing:border-box}
html,body{width:1200px;height:4500px;overflow:hidden}
body{
  font-family:"Montserrat",sans-serif;
  color:var(--white);
  position:relative;
  background:linear-gradient(180deg,#5d86c4 0%,#b7a9cf 9%,#d9d3e4 15%,#c9cfdc 24%,#3e7aa9 30%,#1d4f6c 36%,#2c7b7e 44%,#5a8e5a 55%,#3a6b3a 65%,#6f9a4f 75%,#2f5b2b 88%,#3f6e34 100%);
}
.email{position:absolute;left:150px;top:124px;width:900px}
.block{position:absolute;left:0;width:900px}
.photo{position:absolute}
.hero{top:0;height:714px;background:linear-gradient(90deg,#f1f0ee 0%,#ecebe9 45%,#e9d6c9 70%,#eae6e2 100%)}
.brand{position:absolute;left:30px;top:295px;display:flex;align-items:center;gap:16px;color:#3a3a3a;font-weight:600;font-size:52px;letter-spacing:1px}
.brand-dot{width:80px;height:80px;border-radius:50%;background:#3a3a3a}
.welcome{top:714px;height:545px;background:var(--leaf);text-align:center}
h2{font-weight:600;font-size:46px;line-height:1.1}
.rule{width:48px;height:4px;background:var(--white);margin:22px auto 0}
.rule.left{margin-left:0}
.welcome h2{margin-top:98px}
.welcome p{width:708px;margin:22px auto 0;font-weight:300;font-size:23px;line-height:42px;text-align:justify;text-align-last:center}
.features{top:1259px;height:275px;display:flex}
.feature{width:300px;text-align:center;padding-top:56px}
.feature:nth-child(odd){background:var(--mint)}
.feature:nth-child(even){background:var(--leaf)}
.feature h3{font-weight:600;font-size:30px}
.feature p{font-weight:300;font-size:23px;line-height:36px;margin:14px 24px 0}
.service{top:1534px;height:622px;background:linear-gradient(120deg,#1d6a4f 0%,#3b2c20 40%,#8a6a52 65%,#6c5443 100%)}
.panel{position:absolute;padding:34px 32px 0}
.panel h2{font-size:46px}
.panel p{font-weight:300;font-size:23px;line-height:37.5px;margin-top:30px;text-align:justify}
.service .panel{left:449px;top:235px;width:451px;height:387px;background:rgba(169,207,56,.93)}
.products{top:2156px;height:620px;background:linear-gradient(160deg,#e9ece6 0%,#d8c6a8 40%,#9a6a3c 60%,#c8a070 80%,#4f7a3a 100%)}
.products .panel{left:0;top:0;width:449px;height:387px;background:var(--mint);padding-top:38px}
.promo{top:2776px;height:415px;background:radial-gradient(ellipse at 70% 20%,#1b241c 0%,#263828 55%,var(--forest) 100%);text-align:center}
.promo h2{margin-top:112px}
.promo .code{font-weight:400;font-size:44px;margin-top:22px;letter-spacing:.5px}
.promo .note{font-weight:400;font-size:23px;margin-top:6px}
.duo{top:3191px;height:414px}
.duo-left{left:0;top:0;width:474px;height:414px;background:linear-gradient(135deg,#e4d3c6 0%,#c9a48c 50%,#b88e74 100%)}
.duo-right{left:474px;top:0;width:426px;height:414px;background:linear-gradient(135deg,#6b4a32 0%,#c79a6e 45%,#e2c7a5 70%,#2f8a6a 100%)}
.subscribe{top:3605px;height:620px;background:var(--mint);text-align:center}
.subscribe h2{margin-top:76px}
.signup{width:680px;margin:42px auto 0}
.field{display:block;width:680px;height:72px;background:var(--field);color:var(--field-text);font-size:23px;text-align:left;padding:0 27px;line-height:72px;margin-bottom:15px;font-family:inherit}
.submit{display:block;width:680px;height:72px;background:var(--leaf);color:var(--white);font-weight:600;font-size:25px;line-height:72px}
.social{display:flex;justify-content:center;gap:32px;margin-top:42px}
.social span{width:18px;height:18px;border-radius:50%;background:var(--white)}
.connect{font-size:20px;margin-top:10px}
.legal{position:absolute;left:0;width:1200px;top:4408px;text-align:center;font-size:21px;font-weight:400}
</style>
</head>
<body>
<main class="email">
  <section class="block hero" role="img" aria-label="Woman with towel-wrapped hair receiving a relaxing facial massage">
    <div class="brand"><span class="brand-dot"></span>Tovami Medispa</div>
  </section>

  <section class="block welcome">
    <h2>Welcome To Tovami Medispa</h2>
    <div class="rule"></div>
    <p>Lorem ipsum dolor sit amet, consectetur adipiscing elit, sed do eiusmod tempor incididunt ut labore et dolore magna aliqua. Ut enim ad minim veniam, quis nostrud exercitation ullamco laboris nisi ut aliquip ex ea commodo consequat. Duis aute irure dolor in reprehenderit in voluptate velit esse cillum dolore eu fugiat nulla pariatur.</p>
  </section>

  <section class="block features">
    <div class="feature"><h3>Lorem ipsum</h3><p>Lorem ipsum dolor sit amet, consectetur adipiscing</p></div>
    <div class="feature"><h3>Lorem ipsum</h3><p>Lorem ipsum dolor sit amet, consectetur adipiscing</p></div>
    <div class="feature"><h3>Lorem ipsum</h3><p>Lorem ipsum dolor sit amet, consectetur adipiscing</p></div>
  </section>

  <section class="block service" role="img" aria-label="Therapist giving a back massage in a candle-lit treatment room">
    <div class="panel">
      <h2>What We Do</h2>
      <div class="rule left"></div>
      <p>Lorem ipsum dolor sit amet, consectetur adipiscing elit, sed do eiusmod tempor incididunt ut labore et dolore magna aliqua.</p>
    </div>
  </section>

  <section class="block products" role="img" aria-label="Amber pump bottles and skincare jars on a wooden tray with towels and leaves">
    <div class="panel">
      <h2>Products</h2>
      <div class="rule left"></div>
      <p>Lorem ipsum dolor sit amet, consectetur adipiscing elit, sed do eiusmod tempor incididunt ut labore et dolore magna aliqua.</p>
    </div>
  </section>

  <section class="block promo">
    <h2>Use Promo Code</h2>
    <div class="rule"></div>
    <div class="code">TOVAMIMEDISPA2021</div>
    <div class="note">to save 50% on your Treatment</div>
  </section>

  <section class="block duo">
    <div class="photo duo-left" role="img" aria-label="Hands massaging a client's bare back"></div>
    <div class="photo duo-right" role="img" aria-label="Woman with long hair receiving a hair treatment"></div>
  </section>

  <section class="block subscribe">
    <h2>Subscribe Our Newsletter</h2>
    <div class="rule"></div>
    <div class="signup">
      <div class="field">Name</div>
      <div class="field">Email Address</div>
      <div class="submit">Subscribe Now</div>
    </div>
    <div class="social" aria-label="Social links"><span></span><span></span><span></span></div>
    <div class="connect">Connect With Us</div>
  </section>
</main>
<footer class="legal">© Copyrights.2021.The Company Name.All Rights Reserved</footer>
</body>
</html>
```